Graphic Design/Logo Needed for Ear Drops Bottle

We have an Ear Drop Medication that we need to create a new label for. We will use a retro picture of a Doctor (Dr. Bellamy) and the name of the product is Mighty Lobe. There is no official logo, so we will want to create a retro, basic logo for Mighty Lobe and use the retro picture. Front portion of the label is Size is 1.5" in height, and about 1.375" Width. this is a small tube similar in size to eye drops. We will be looking for just the logo portion and what you will see on the front of the bottle.

Target Market(s)

Medical Container

Industry/Entity Type

Medical

Font styles to use
Serif
Sans Serif

Colors
0054AA
0677BA
7BADD7
CADEEF
E8F1F8
FFF300
FFF600
FEFA6F
FFFEC7
FFFEE8

Requirements
Must have
• Picture of Dr. Bellamy, "Mighty Lobe", Dr. Bellamy's Ear Solution
Nice to have
• Retro Style or Modern with Retro Feel, Clean and engaging

```html
<!DOCTYPE html>
<html lang="en">
<head>
<meta charset="utf-8">
<title>Mighty Lobe – Ear Solution Label</title>
<link rel="stylesheet" href="https://fonts.googleapis.com/css2?family=Montserrat:wght@600;700&family=Saira+Extra+Condensed:wght@600;700&display=swap">
<style>
  :root {
    --navy: #0d3f73;
    --blue: #0677ba;
    --pale: #cadeef;
    --ice: #e8f1f8;
    --yellow: #f5e926;
    --white: #ffffff;
    --stage: #ffffff;
  }
  * { box-sizing: border-box; margin: 0; padding: 0; }
  html, body {
    width: 1200px; height: 773px; overflow: hidden;
    background: var(--stage);
  }
  .canvas { position: relative; width: 1200px; height: 773px; }
  .label {
    position: absolute; left: 347px; top: 112px;
    width: 506px; height: 550px;
    background: var(--pale);
    overflow: hidden;
  }
  .label__diagonal { position: absolute; inset: 0; }
  .brand {
    position: absolute; left: 90px; top: 60px;
    width: 342px; height: 94px;
    overflow: visible;
  }
  .brand__text {
    font-family: "Saira Extra Condensed", "Arial Narrow", sans-serif;
    font-weight: 700; font-size: 100px;
    fill: var(--navy);
  }
  .brand__rule {
    position: absolute; left: 91px; top: 160px;
    width: 340px; height: 9px;
    background: var(--yellow);
  }
  .tagline {
    position: absolute; left: 91px; top: 188px;
    font-family: "Montserrat", Arial, sans-serif;
    font-weight: 700; font-size: 22px; line-height: 29px;
    color: var(--navy);
    white-space: nowrap;
  }
  .doctor-portrait {
    position: absolute; left: 278px; top: 189px;
    width: 228px; height: 361px;
    background: linear-gradient(160deg, var(--navy) 0%, #2a5d92 55%, var(--navy) 100%);
    border-radius: 110px 110px 0 0;
  }
  .net-weight {
    position: absolute; left: 84px; top: 468px;
    display: flex; align-items: center; gap: 5px;
    font-family: "Saira Extra Condensed", "Arial Narrow", sans-serif;
    font-weight: 600; font-size: 19px; line-height: 1;
    color: var(--navy);
    white-space: nowrap;
  }
  .net-weight__badge {
    flex: none;
    width: 46px; height: 46px; border-radius: 50%;
    background: var(--navy); color: var(--white);
    display: flex; align-items: center; justify-content: center;
    font-size: 18px; font-weight: 700; letter-spacing: -0.5px;
    white-space: nowrap;
  }
</style>
</head>
<body>
<main class="canvas">
  <section class="label">
    <svg class="label__diagonal" width="506" height="550" viewBox="0 0 506 550" aria-hidden="true">
      <polygon points="0,550 506,365 506,550" fill="var(--white)"/>
    </svg>

    <svg class="brand" width="342" height="94" viewBox="0 0 342 94" role="heading" aria-level="1" aria-label="MightyLobe">
      <text class="brand__text" x="1" y="86" textLength="340" lengthAdjust="spacingAndGlyphs">MightyLobe</text>
    </svg>
    <div class="brand__rule"></div>

    <p class="tagline">Dr Bellamy’s<br>Ear Solution</p>

    <div class="doctor-portrait" role="img" aria-label="Retro two-tone navy portrait of Dr. Bellamy wearing a head mirror, shirt and tie"></div>

    <div class="net-weight">
      <span>Nt. Wt.</span>
      <span class="net-weight__badge">2 oz</span>
      <span>59 ml</span>
    </div>
  </section>
</main>
</body>
</html>
```